Aunt Roula's Bakery

I am about to create a luxury boutique that specializes in cake baking and cupcake
and ready for parties and special events and order delivery
the logo has already made

Boutique

Email:auntroulasbakery@mailbox-example.net
Instagram: aunt_roula_bakery
Twitter: xxxxxxx
WhatsApp: xxxxxxx

Requirements
Must have
• luxury design

```html
<!DOCTYPE html>
<html lang="en">
<head>
<meta charset="utf-8">
<title>Aunt Roula's Bakery — Business Card</title>
<link rel="stylesheet" href="https://fonts.googleapis.com/css2?family=Lato:wght@400;700;900&display=swap">
<style>
  :root {
    --backdrop: #ece8e3;
    --card: #f7f7f6;
    --rose: #d9a5b5;
    --rose-band: #cf9aab;
    --rose-text: #e3a7ba;
    --slate: #8a8d8c;
    --slate-dark: #6f7271;
    --white: #ffffff;
  }
  * { margin: 0; padding: 0; box-sizing: border-box; }
  html, body {
    width: 1200px;
    height: 780px;
    overflow: hidden;
    background: var(--backdrop);
    font-family: "Lato", "Helvetica Neue", Arial, sans-serif;
  }
  .canvas {
    position: relative;
    width: 1200px;
    height: 780px;
    display: flex;
    align-items: center;
    justify-content: center;
  }
  .business-card {
    position: relative;
    width: 440px;
    height: 730px;
    background: var(--card);
    box-shadow: 0 6px 24px rgba(0,0,0,0.12);
    display: flex;
    flex-direction: column;
  }
  .card-body {
    flex: 1;
    padding: 70px 50px 0;
    display: flex;
    flex-direction: column;
  }
  .brand {
    display: flex;
    align-items: center;
    justify-content: center;
    gap: 14px;
    margin-bottom: 120px;
  }
  .brand-dot {
    width: 46px;
    height: 46px;
    border-radius: 50%;
    background: var(--rose);
    flex-shrink: 0;
  }
  .brand-name {
    font-size: 30px;
    font-weight: 400;
    color: var(--slate);
    letter-spacing: 1px;
  }
  .person-name {
    font-size: 34px;
    font-weight: 900;
    color: var(--slate);
    letter-spacing: 0.5px;
    line-height: 1;
  }
  .person-role {
    font-size: 22px;
    font-weight: 400;
    color: var(--rose-text);
    margin-top: 4px;
    letter-spacing: 0.5px;
  }
  .contact-list {
    list-style: none;
    margin-top: 60px;
  }
  .contact-item {
    display: flex;
    align-items: center;
    gap: 14px;
    font-size: 22px;
    color: var(--slate-dark);
    line-height: 1.35;
    letter-spacing: 0.5px;
  }
  .contact-mark {
    width: 22px;
    height: 22px;
    background: var(--rose);
    flex-shrink: 0;
  }
  .contact-email {
    margin-top: 8px;
    font-size: 17px;
    font-weight: 700;
    color: var(--slate-dark);
    letter-spacing: 0.3px;
  }
  .card-band {
    height: 135px;
    background: var(--rose-band);
    display: flex;
    align-items: center;
    padding-left: 50px;
  }
  .website {
    font-size: 24px;
    color: var(--white);
    letter-spacing: 1px;
  }
</style>
</head>
<body>
  <main class="canvas">
    <article class="business-card">
      <section class="card-body">
        <header class="brand">
          <span class="brand-dot"></span>
          <span class="brand-name">Aunt Roula's Bakery</span>
        </header>
        <h1 class="person-name">Employee Name</h1>
        <p class="person-role">Managing Director</p>
        <ul class="contact-list">
          <li class="contact-item"><span class="contact-mark"></span>aunt_roula_bakery</li>
          <li class="contact-item"><span class="contact-mark"></span>aunt_roula_bakery</li>
          <li class="contact-item"><span class="contact-mark"></span>aunt_roula_bakery</li>
        </ul>
        <p class="contact-email">auntroulasbakery@mailbox-example.net</p>
      </section>
      <footer class="card-band">
        <p class="website">www.yourwebsite.com</p>
      </footer>
    </article>
  </main>
</body>
</html>
```